Home Page for a Swiss based start up company, trading Natural & Health food ingredients (B2B)

I would like to create a home page for my new start up company (Veltrana Swiss AG), the main field of activity is the trading and marketing of Natural and Health food ingredients towards the functional Food and Food supplements industry. (B2B).
Target Market : Functional Food and Food Supplement Manufacturers (B2B) based in Switzerland and Europe
The values I would like to convey are :
- sourcing of natural and health ingredients, (example : natural plant extracts, Omega 3, plant proteins, natural vitamins, vegan food ingredients...etc)
- Health & Nutritional Health
- Eco-friendly and Sustainability
- High Quality Standard in term of products and logistic services
- Trust and reliability
- Flexibility & speed to market
-Technical advice for the development of new products

The site will be translated in 3 languages (German, French, English)
Number of web pages : 5 : Home, About us, Products, Our Services, Contact

See here below attached Logo file.

Here some link of websites which can be taken as benchmark or source of inspiration
- https://quorbelix.com
- https://www.dralvimo.com/

Target Market(s)

Manufacturers of Functional Foods and Food Supplements in Switzerland and Europe (B2B)

Industry/Entity Type

B2B Trading of Natural & Health Ingredients

Coding

Number of Pages Required

Font styles to use
Sans Serif

Colors
0054AA
0677BA
7BADD7
CADEEF
E8F1F8
0094D4
00A9DD
6FCCEA
C7EBF8
E9F6FB
00AB8E
00BBA5
67D7C9
C6EFE9
E9F9F6
59FF00
82FF00
B8FF75
E3FFCB
F4FFEA
FFF300
FFF600
FEFA6F
FFFEC7
FFFEE8
FFC000
F8CF3A
FAE287
FDF2CF
FEFAEE
F0912C
F2A743
F7CA91
FBE8D2
FDF5EE
EE7325
F08F49
F5BC92
FAE3D3
FDF4ED

Requirements
Must have
• inspiration towards nature, sustainability, vegan food, functional food & beverages, food supplements, nutritional health, low carbon footprint
Should not have
• animals, chemistry, food additives

```html
<!DOCTYPE html>
<html lang="en">
<head>
<meta charset="utf-8">
<title>Veltrana Swiss AG – Natural &amp; Health Food Ingredients</title>
<link href="https://fonts.googleapis.com/css2?family=Raleway:wght@400;500;600&family=Lato:wght@400;700&display=swap" rel="stylesheet">
<style>
:root{
  --mint-bg:#f0fbe5;
  --orange:#ee7325;
  --orange-soft:#fae3d3;
  --teal:#00ab8e;
  --teal-border:#67d7c9;
  --blue:#0054aa;
  --blue-mid:#0677ba;
  --ink:#222;
  --text:#555;
  --white:#fff;
}
*{margin:0;padding:0;box-sizing:border-box}
html,body{width:1200px;height:3957px;overflow:hidden}
body{position:relative;background:var(--white);font-family:'Lato',sans-serif;color:var(--text)}
.abs{position:absolute}
.display{font-family:'Raleway',sans-serif;font-weight:400;color:var(--ink)}
.rule{position:absolute;height:3px;width:77px;background:var(--orange)}
.center{text-align:center;left:0;width:1200px}

/* header + hero */
.top-area{position:absolute;left:0;top:0;width:1200px;height:1761px;background:var(--mint-bg)}
.logo{font-family:'Raleway',sans-serif;font-weight:500;color:var(--ink);font-size:31px;letter-spacing:.5px}
.nav{position:absolute;top:33px;left:436px;display:flex;gap:30px;font-size:15px;color:#333}
.nav .active{color:var(--orange);border-bottom:2px solid var(--orange);padding-bottom:6px}
.lang{position:absolute;left:1009px;top:26px;width:80px;height:35px;background:var(--blue);color:#fff;border-radius:5px;font-size:13px;display:flex;align-items:center;justify-content:center}
.eyebrow{font-size:17px;color:var(--blue-mid);letter-spacing:.2px}
.hero-title{font-size:56px}
.hero-sub{font-size:14px;line-height:26px;color:#555}
.btn{position:absolute;background:var(--orange);color:#fff;border-radius:24px;display:flex;align-items:center;justify-content:center;font-size:16px}
.play{position:absolute;left:291px;top:423px;width:64px;height:64px;border:3px solid var(--orange);border-radius:50%;display:flex;align-items:center;justify-content:center}
.play span{width:44px;height:44px;border-radius:50%;background:var(--orange);display:flex;align-items:center;justify-content:center}

/* services */
.section-title{font-size:43px}
.card{position:absolute;top:844px;width:313px;height:354px;background:#fff;border-radius:4px;box-shadow:0 4px 16px rgba(0,0,0,.08);text-align:center}
.card.featured{border:1.5px solid var(--teal-border)}
.icon-ring{width:110px;height:110px;margin:24px auto 0;border:2px dotted #888;border-radius:50%;padding:6px}
.icon-ring div{width:100%;height:100%;border-radius:50%;background:var(--orange-soft);display:flex;align-items:center;justify-content:center}
.card h3{font-family:'Lato',sans-serif;font-weight:500;font-size:22px;color:var(--ink);margin-top:20px}
.card p{font-size:14px;line-height:26px;margin:12px 40px 0}
.read{font-size:14px;color:var(--ink);font-weight:700;margin-top:14px;display:flex;justify-content:center;align-items:center;gap:6px}

/* about */
.about-photo{position:absolute;left:0;top:1214px;width:838px;height:547px;background:radial-gradient(ellipse at 45% 50%,#e6b24a 0%,#c98f4a 30%,#a7bb6a 55%,rgba(240,251,229,0) 80%)}
.body-copy{font-size:14px;line-height:26px;text-align:justify;color:#555}

/* values */
.values{position:absolute;left:0;top:1761px;width:1200px;height:608px;background:var(--teal)}
.value{position:absolute;display:flex;align-items:center;gap:14px;color:#fff;font-size:14px;font-weight:700;line-height:26px}
.value .ic{width:88px;height:88px;border-radius:50%;background:#fff;display:flex;align-items:center;justify-content:center;flex:none}

/* blog */
.post{position:absolute;top:2543px;width:313px;height:384px;background:#fff;box-shadow:0 4px 16px rgba(0,0,0,.08);text-align:center}
.post.faded{opacity:.3}
.post .ph{margin:5px;height:184px}
.post h3{font-family:'Lato',sans-serif;font-weight:500;font-size:24px;color:var(--ink);margin-top:14px}
.post p{font-size:14px;line-height:26px;margin:6px 34px 0}
.meta{position:absolute;left:25px;right:25px;top:332px;border-top:1px solid #e5e5e5;padding-top:12px;display:flex;justify-content:space-between;font-size:13px;color:var(--orange)}

/* contact */
.contact{position:absolute;left:109px;top:3011px;width:980px;height:451px;border:2px solid var(--teal);border-radius:6px;background:rgba(255,255,255,.85)}
.field{position:absolute;border-bottom:1px solid #bbb;font-family:Arial,sans-serif;font-size:13px;color:#777;padding:0 0 12px 10px}

/* footer */
.footer{position:absolute;left:0;top:3546px;width:1200px;height:411px;background:var(--blue);color:#fff}
.footer h4{font-family:'Lato',sans-serif;font-size:20px;font-weight:700;position:absolute}
.links{position:absolute;left:541px;top:138px;list-style:none;font-size:14px;line-height:26px}
.links li::before{content:"»";margin-right:20px}
</style>
</head>
<body>

<div class="top-area">
  <div class="abs logo" style="left:109px;top:24px">Veltrana Swiss AG</div>
  <nav class="nav"><span class="active">Home +</span><span>About us +</span><span>Services +</span><span>Values +</span><span>Blog +</span><span>Contact us</span></nav>
  <div class="lang">Eng &#8964;</div>

  <div class="abs" role="img" aria-label="Overhead photo of fresh vegetables, fruit, avocado, lentils and beans on a cutting board" style="left:584px;top:61px;width:616px;height:692px;border-radius:60% 0 0 60% / 55% 0 0 45%;background:radial-gradient(circle at 40% 40%,#f29a4a 0%,#8fbf4a 35%,#4f8a2e 60%,#d8432e 85%)"></div>

  <div class="abs eyebrow" style="left:110px;top:255px">TRADING NATURAL &amp; HEALTH FOOD INGREDIENTS</div>
  <div class="abs display hero-title" style="left:106px;top:290px">Veltrana Swiss AG</div>
  <div class="abs hero-sub" style="left:110px;top:364px;width:360px">Lorem ipsum dolor sit amet, consectetur adipiscing elit, sed do eiusmod</div>
  <div class="btn" style="left:110px;top:433px;width:156px;height:43px">Our Services</div>
  <div class="play"><span><svg width="12" height="14" viewBox="0 0 12 14"><path d="M0 0L12 7L0 14Z" fill="#fff"/></svg></span></div>

  <!-- services -->
  <div class="rule" style="left:561px;top:716px"></div>
  <div class="abs display section-title center" style="top:733px">OUR SERVICES</div>
  <div class="abs center" style="top:800px;font-size:14px;color:#333">Lorem ipsum dolor sit amet, consectetur adipiscing elit, sed do eiusmod tempor incididunt</div>

  <div class="card" style="left:110px">
    <div class="icon-ring"><div><svg width="50" height="50" viewBox="0 0 50 50"><path d="M6 16A19 19 0 0 0 44 16Z" fill="var(--orange)"/><path d="M11 18A14 14 0 0 0 39 18" fill="none" stroke="#fff" stroke-width="2"/></svg></div></div>
    <h3>Natural Food</h3>
    <p>Lorem ipsum dolor sit amet, consectetur adipiscing elit, sed do eiusmod tempor incididunt ut labore et dolore.</p>
    <div class="read">Read more <svg width="20" height="20" viewBox="0 0 20 20"><rect x="4" y="4" width="12" height="12" transform="rotate(45 10 10)" fill="var(--orange)"/><path d="M8 10h4M10 8l2 2-2 2" stroke="#fff" stroke-width="1.5" fill="none"/></svg></div>
  </div>
  <div class="card featured" style="left:443px">
    <div class="icon-ring"><div><svg width="50" height="40" viewBox="0 0 50 40"><path d="M24 34C14 34 6 24 4 10C16 12 24 22 24 34Z M26 34C36 34 44 24 46 10C34 12 26 22 26 34Z" fill="var(--orange)"/></svg></div></div>
    <h3>Biologically Safe</h3>
    <p>Lorem ipsum dolor sit amet, consectetur adipiscing elit, sed do eiusmod tempor incididunt ut labore et dolore.</p>
    <div class="read">Read more <svg width="20" height="20" viewBox="0 0 20 20"><rect x="4" y="4" width="12" height="12" transform="rotate(45 10 10)" fill="var(--orange)"/><path d="M8 10h4M10 8l2 2-2 2" stroke="#fff" stroke-width="1.5" fill="none"/></svg></div>
  </div>
  <div class="card" style="left:776px">
    <div class="icon-ring"><div><svg width="40" height="50" viewBox="0 0 40 50"><path d="M8 14H32L28 46H12Z" fill="none" stroke="var(--orange)" stroke-width="3"/><path d="M22 14L28 2" stroke="var(--orange)" stroke-width="3"/><circle cx="14" cy="14" r="6" fill="var(--orange)"/></svg></div></div>
    <h3>100% Natural Juice</h3>
    <p>Lorem ipsum dolor sit amet, consectetur adipiscing elit, sed do eiusmod tempor incididunt ut labore et dolore.</p>
    <div class="read">Read more <svg width="20" height="20" viewBox="0 0 20 20"><rect x="4" y="4" width="12" height="12" transform="rotate(45 10 10)" fill="var(--orange)"/><path d="M8 10h4M10 8l2 2-2 2" stroke="#fff" stroke-width="1.5" fill="none"/></svg></div>
  </div>

  <!-- about -->
  <div class="about-photo" role="img" aria-label="Paper grocery bag spilling fruit, vegetables, nuts and herbs"></div>
  <div class="rule" style="left:612px;top:1284px"></div>
  <div class="abs display section-title" style="left:610px;top:1300px">ABOUT US</div>
  <p class="abs body-copy" style="left:612px;top:1356px;width:476px">Lorem ipsum dolor sit amet, consectetur adipiscing elit, sed do eiusmod tempor incididunt ut labore et dolore magna aliqua. Ut enim ad minim veniam, quis nostrud exercitation ullamco laboris nisi ut aliquip ex ea commodo consequat. Duis aute irure dolor in reprehenderit in voluptate velit esse cillum dolore eu fugiat nulla pariatur.</p>
  <p class="abs body-copy" style="left:612px;top:1509px;width:476px">Excepteur sint occaecat cupidatat non proident, sunt in culpa qui officia deserunt mollit anim id est laborum. Lorem ipsum dolor sit amet, consectetur adipiscing elit, sed do eiusmod tempor incididunt ut labore et dolore magna aliqua.</p>
  <div class="btn" style="left:612px;top:1633px;width:153px;height:42px;font-size:15px">Learn more &#10148;</div>
</div>

<!-- values -->
<section class="values">
  <div class="abs" style="left:561px;top:86px;width:77px;height:3px;background:#fff"></div>
  <div class="abs display section-title center" style="top:103px;color:#fff">OUR VALUES</div>

  <div class="value" style="left:110px;top:180px"><div class="ic"><svg width="44" height="40" viewBox="0 0 44 40"><path d="M22 38L4 20A11 11 0 0 1 22 6A11 11 0 0 1 40 20Z" fill="var(--teal)"/><path d="M6 20H16L19 13L24 27L27 20H38" stroke="#fff" stroke-width="2.5" fill="none"/></svg></div>Sourcing of natural and<br>health ingredients</div>
  <div class="value" style="left:475px;top:180px"><div class="ic"><svg width="40" height="44" viewBox="0 0 40 44"><rect x="6" y="10" width="18" height="32" rx="3" fill="var(--teal)"/><rect x="9" y="3" width="12" height="6" fill="var(--teal)"/><rect x="26" y="22" width="10" height="20" rx="2" fill="var(--teal)"/></svg></div>Health &amp; Nutritional<br>Health</div>
  <div class="value" style="left:838px;top:180px"><div class="ic"><svg width="44" height="40" viewBox="0 0 44 40"><path d="M4 30C14 26 22 34 40 26" stroke="var(--teal)" stroke-width="3" fill="none"/><path d="M22 22C14 22 12 14 12 8C20 8 22 14 22 22ZM22 22C30 22 34 14 34 6C26 6 22 12 22 22Z" fill="var(--teal)"/></svg></div>Eco-friendly and<br>Sustainability</div>

  <div class="value" style="left:110px;top:309px"><div class="ic"><svg width="50" height="36" viewBox="0 0 50 36"><rect x="2" y="6" width="30" height="20" fill="var(--teal)"/><path d="M32 12H42L48 20V26H32Z" fill="var(--teal)"/><circle cx="12" cy="30" r="5" fill="var(--teal)" stroke="#fff" stroke-width="2"/><circle cx="40" cy="30" r="5" fill="var(--teal)" stroke="#fff" stroke-width="2"/></svg></div>High Quality Standard in term<br>of products and logistic services</div>
  <div class="value" style="left:475px;top:309px"><div class="ic"><svg width="40" height="44" viewBox="0 0 40 44"><path d="M20 2L36 8V22C36 32 28 40 20 42C12 40 4 32 4 22V8Z" fill="none" stroke="var(--teal)" stroke-width="3"/><path d="M13 22L18 27L28 16" stroke="var(--teal)" stroke-width="3" fill="none"/></svg></div>Trust and reliability</div>
  <div class="value" style="left:838px;top:309px"><div class="ic"><svg width="44" height="40" viewBox="0 0 44 40"><path d="M14 14L20 4M30 14L24 4" stroke="var(--teal)" stroke-width="3"/><path d="M2 14H42V18H38L34 38H10L6 18H2Z" fill="var(--teal)"/><path d="M16 22V32M22 22V32M28 22V32" stroke="#fff" stroke-width="2.5"/></svg></div>Flexibility &amp; speed to<br>market</div>

  <div class="value" style="left:110px;top:438px"><div class="ic"><svg width="44" height="44" viewBox="0 0 44 44"><circle cx="22" cy="22" r="13" fill="none" stroke="var(--teal)" stroke-width="8" stroke-dasharray="6 4"/><circle cx="22" cy="22" r="5" fill="var(--teal)"/></svg></div>Technical advice for the<br>development of new products</div>
  <div class="value" style="left:475px;top:438px"><div class="ic"><svg width="40" height="44" viewBox="0 0 40 44"><path d="M20 2L36 8V22C36 32 28 40 20 42C12 40 4 32 4 22V8Z" fill="none" stroke="var(--teal)" stroke-width="3"/><rect x="13" y="20" width="14" height="11" fill="var(--teal)"/><path d="M15 20V16A5 5 0 0 1 25 16V20" stroke="var(--teal)" stroke-width="2.5" fill="none"/></svg></div>Security of supply</div>

  <div class="abs" role="img" aria-label="Split cocoa pod with leaves" style="left:791px;top:430px;width:270px;height:238px;border-radius:50% 50% 45% 55%/60% 60% 40% 40%;background:radial-gradient(ellipse at 45% 55%,#f6ecd6 0%,#f0c23a 45%,#d99a1e 75%);transform:rotate(-18deg)"></div>
</section>

<!-- blog -->
<div class="rule" style="left:561px;top:2454px"></div>
<div class="abs display section-title center" style="top:2471px">LATEST BLOG</div>

<div class="post faded" style="left:-225px"><div class="ph" style="background:#d9ddd0"></div><h3>Nemo enim ipsam</h3></div>
<div class="post" style="left:110px">
  <div class="ph" role="img" aria-label="Cook preparing vegetables in a kitchen" style="background:linear-gradient(135deg,#8a6a4a,#d0a070 50%,#6b4c33)"></div>
  <h3>Nemo enim ipsam</h3>
  <p>Lorem ipsum dolor sit amet, consec tetur adipiscing elit, sed do eiusmod tempor incididunt</p>
  <div class="meta"><span>&#9823; by John doe</span><span>&#128197; Jan 22, 2022</span></div>
</div>
<div class="post" style="left:443px">
  <div class="ph" role="img" aria-label="Chef holding fresh vegetables at a counter" style="background:linear-gradient(135deg,#3a3a34,#9a8a70 50%,#5b7a3a)"></div>
  <h3>Nemo enim ipsam</h3>
  <p>Lorem ipsum dolor sit amet, consec tetur adipiscing elit, sed do eiusmod tempor incididunt</p>
  <div class="meta"><span>&#9823; by John doe</span><span>&#128197; Jan 22, 2022</span></div>
</div>
<div class="post" style="left:776px">
  <div class="ph" role="img" aria-label="Fresh fruit and vegetables beside a health notebook" style="background:linear-gradient(135deg,#c8302a,#e8b030 35%,#5a9a3a 60%,#2a2a2a)"></div>
  <h3>Nemo enim ipsam</h3>
  <p>Lorem ipsum dolor sit amet, consec tetur adipiscing elit, sed do eiusmod tempor incididunt</p>
  <div class="meta"><span>&#9823; by John doe</span><span>&#128197; Jan 22, 2022</span></div>
</div>
<div class="post faded" style="left:1109px"><div class="ph" style="background:#d9ddd0"></div><h3>Nemo enim ipsam</h3></div>

<!-- contact -->
<div class="abs" role="img" aria-label="Sliced cucumbers, tomatoes, radishes and greens" style="left:0;top:3380px;width:1200px;height:166px;background:linear-gradient(180deg,#fff 0%,#e8f2df 40%,#b9d79a 70%,#e58a80 100%)"></div>
<div class="contact">
  <div class="rule" style="left:451px;top:53px"></div>
  <div class="abs display section-title" style="left:0;width:976px;text-align:center;top:68px">GET IN TOUCH</div>
  <div class="field" style="left:94px;top:160px;width:233px">Your name *</div>
  <div class="field" style="left:376px;top:160px;width:231px">Phone *</div>
  <div class="field" style="left:653px;top:160px;width:234px">Email address *</div>
  <div class="field" style="left:94px;top:288px;width:793px">Message *</div>
  <div class="btn" style="left:410px;top:347px;width:162px;height:44px;font-family:Arial,sans-serif;font-weight:700;font-size:13px">SUBMIT NOW</div>
</div>

<!-- footer -->
<footer class="footer">
  <div class="abs logo" style="left:109px;top:82px;color:#fff">Veltrana Swiss AG</div>
  <p class="abs" style="left:110px;top:176px;width:360px;font-size:14px;line-height:26px">Lorem ipsum dolor sit amet, consectetur adipiscing elit, sed do eiusmod tempor incididunt ut labore et dolore magna aliqua. Lorem ipsum dolor sit amet, consectetur adipiscing elit, sed do eiusmod tempor</p>
  <h4 style="left:541px;top:82px">Quick Links</h4>
  <ul class="links"><li>Home</li><li>About us</li><li>Services</li><li>Testimonials</li><li>Blog</li><li>Contact us</li></ul>
  <h4 style="left:747px;top:82px">Our Gallery</h4>
  <div class="abs" role="img" aria-label="Salmon and vegetables" style="left:747px;top:135px;width:167px;height:83px;background:linear-gradient(135deg,#e8734a,#f0c0a0,#7aa050)"></div>
  <div class="abs" role="img" aria-label="Chef plating food" style="left:921px;top:135px;width:167px;height:83px;background:linear-gradient(135deg,#4a4038,#9a8a78,#3a3430)"></div>
  <div class="abs" role="img" aria-label="Kitchen team at work" style="left:747px;top:225px;width:167px;height:83px;background:linear-gradient(135deg,#d8d0c4,#a08868,#e8e0d8)"></div>
  <div class="abs" role="img" aria-label="Ingredients on a wooden board" style="left:921px;top:225px;width:167px;height:83px;background:linear-gradient(135deg,#2a2a28,#8a5a30,#4a6a30)"></div>
  <div class="abs center" style="top:352px;font-size:14px">&copy; Copyrights.2022.The Company Name.All Rights Reserved</div>
</footer>

</body>
</html>
```